Modern Business Card For A Digital Advertising Company

I'll be print on the Pell Prints Velour paper http://us.pellprints.com/products/velour/business-cards.html
Need's to be modern and use the color palette of the logo or gray scales. I think integrating the pixelation of the logo in to the card and having it wrap from one side to the other could be interesting. My company provides ad operations, web development, and number of other services to websites around the world. You can see my website at http://www.zantorhq.com
Contact info on the card needs to have
Owen Lasko
President
p.318.204.6637
owen@zantorhq.com
http://www.zantorhq.com
Doesn't necessarily need to be in that order
Website owners
Business

```html
<!DOCTYPE html>
<html lang="en">
<head>
<meta charset="utf-8">
<title>Zantor – Business Card</title>
<link href="https://fonts.googleapis.com/css2?family=Arimo:ital,wght@0,400;0,700;1,400&family=Open+Sans:wght@400;600&display=swap" rel="stylesheet">
<style>
  :root {
    --page: #d6d6d6;
    --ink-white: #ffffff;
    --ink-dark: #2a2a2a;
    --steel-dark: #1f1f1f;
    --steel-charcoal: #3a3a3a;
    --steel-mid: #a9a9a9;
    --steel-light: #e8e8e8;
    --steel-pale: #c8c8c8;
    --brand-green: #8cc63f;
    --icon-fill: #1a1a1a;
  }
  * { margin: 0; padding: 0; box-sizing: border-box; }
  html, body {
    width: 1200px; height: 911px; overflow: hidden;
    background: var(--page);
  }
  .card {
    position: absolute; left: 113px; top: 151px;
    width: 985px; height: 563px; overflow: hidden;
  }
  .card-backdrop {
    position: absolute; inset: 0;
    background: linear-gradient(90deg,
      var(--steel-dark) 0%,
      var(--steel-charcoal) 48%,
      var(--steel-mid) 60%,
      var(--steel-pale) 100%);
  }

  .title-tag {
    position: absolute; left: 0; top: 165px; width: 158px; height: 40px;
    background: linear-gradient(90deg, var(--steel-mid), var(--ink-white) 70%, var(--steel-light));
    clip-path: polygon(0 0, 100% 0, 94% 100%, 0 100%);
    font-family: "Arimo", Arial, sans-serif; font-style: italic;
    font-size: 26px; color: var(--ink-dark);
    padding-left: 16px; line-height: 42px;
  }
  .person-name {
    position: absolute; left: 164px; top: 158px;
    font-family: "Arimo", Arial, sans-serif; font-weight: 700;
    font-size: 50px; letter-spacing: -1px; color: var(--ink-white);
    line-height: 1;
  }
  .contact-bar {
    position: absolute; left: 0; width: 175px; height: 42px;
    background: linear-gradient(180deg, var(--ink-white), var(--steel-mid) 55%, var(--steel-light));
  }
  .contact-bar.phone { top: 273px; }
  .contact-bar.mail { top: 327px; }
  .contact-bar.web { top: 384px; }

  .contact-icon { position: absolute; left: 160px; width: 44px; height: 44px; }
  .contact-icon.phone { top: 272px; }
  .contact-icon.mail { top: 326px; }
  .contact-icon.web { top: 383px; }

  .contact-text {
    position: absolute; left: 218px;
    font-family: "Open Sans", Arial, sans-serif; color: var(--ink-white);
    line-height: 1; white-space: nowrap;
  }
  .contact-text.phone { top: 275px; font-size: 39px; font-weight: 600; }
  .contact-text.mail { top: 337px; font-size: 22px; }
  .contact-text.web { top: 394px; font-size: 22px; }

  .brand {
    position: absolute; left: 700px; top: 260px;
    display: flex; align-items: center; gap: 14px;
  }
  .brand-square { width: 34px; height: 34px; background: var(--brand-green); }
  .brand-name {
    font-family: "Arimo", Arial, sans-serif; font-weight: 700;
    font-size: 62px; color: var(--brand-green); line-height: 1;
  }
</style>
</head>
<body>
  <main class="card">
    <div class="card-backdrop" role="img" aria-label="Metallic background of angled steel-grey planes, dark on the left fading to light grey on the right"></div>

    <div class="title-tag">President</div>
    <h1 class="person-name">Owen Lasko</h1>

    <div class="contact-bar phone"></div>
    <div class="contact-bar mail"></div>
    <div class="contact-bar web"></div>

    <svg class="contact-icon phone" viewBox="0 0 44 44" aria-label="Phone">
      <circle cx="22" cy="22" r="20" fill="var(--icon-fill)" stroke="var(--ink-white)" stroke-width="2.5"/>
      <rect x="15" y="9" width="14" height="26" rx="2.5" fill="none" stroke="var(--ink-white)" stroke-width="2"/>
      <line x1="17" y1="29" x2="27" y2="29" stroke="var(--ink-white)" stroke-width="1.5"/>
    </svg>
    <svg class="contact-icon mail" viewBox="0 0 44 44" aria-label="Email">
      <circle cx="22" cy="22" r="20" fill="var(--icon-fill)" stroke="var(--ink-white)" stroke-width="2.5"/>
      <text x="22" y="30" text-anchor="middle" font-family="Arimo, Arial, sans-serif" font-size="24" fill="var(--ink-white)">@</text>
    </svg>
    <svg class="contact-icon web" viewBox="0 0 44 44" aria-label="Website">
      <circle cx="22" cy="22" r="20" fill="var(--icon-fill)" stroke="var(--ink-white)" stroke-width="2.5"/>
      <circle cx="22" cy="12" r="3" fill="var(--ink-white)"/>
      <rect x="19.5" y="18" width="5" height="16" rx="1" fill="var(--ink-white)"/>
    </svg>

    <p class="contact-text phone">318.204.6637</p>
    <p class="contact-text mail">owen@zantorhq.com</p>
    <p class="contact-text web">www.zantorhq.com</p>

    <div class="brand">
      <span class="brand-square"></span>
      <span class="brand-name">Zantor</span>
    </div>
  </main>
</body>
</html>
```